Pine Ledge Traders, LLC- Global Beverage Company with 100% Cold Chain Logistics

Hey All, My Name is Dale, I am a young business owner in a competitive export space, but my niche is that I am shipping all of my beer around the world, "100% Cold Chain". This model is more costly, but it protects the integrity of the beer itself and will give folks in foreign countries the best representation of what US Craft Beer has to offer.

I am not a branding guy and don't claim to be one, I am a salesperson first, and will be referring to all of you to create something great that will be memorable.

I am looking for a basic Business Card Design for my Craft Beer Export company. I sell US Craft Beer in several countries around the globe. Austrailia, China, Taiwan, Chile, France, New Zealand... to name a few.

I am looking for a sleek, modern, and fresh design. Quickly!

Thanks for your consideration!

Cheers,

Dale

Target Market(s)

International

Contact Information for Business Card

Dale Corrigan
Founder- Roaming Hops Guy
Dale@PineLedgeTraders.example
@RoamingHopsGuy- Instagram only
www.Pineledgetraders.example
@PineLedgeTradersAU- Instagram Only

Font styles to use
Serif

Colors
0592cd
ffffff

Requirements
Must have
• Name-
• Title-
• Email-
• Social Media Handle-
• Company Website-
Nice to have
• Nice Logo/ Images on Card
Should not have
• Tacky Beer Images

```html
<!DOCTYPE html>
<html lang="en">
<head>
<meta charset="utf-8">
<title>Pine Ledge Traders – Business Card</title>
<link rel="stylesheet" href="https://fonts.googleapis.com/css2?family=Cinzel:wght@400;600;700&family=Roboto:wght@400&display=swap">
<style>
  :root {
    --stage: #ece7df;
    --kraft-light: #cfa26b;
    --kraft-dark: #b7854f;
    --ink: #141210;
    --map-tone: rgba(90, 60, 30, 0.16);
    --rule: rgba(20, 18, 16, 0.55);
  }
  * { box-sizing: border-box; margin: 0; padding: 0; }
  html, body { width: 1200px; height: 900px; overflow: hidden; }
  body { background: var(--stage); position: relative; color: var(--ink); }

  .card {
    position: absolute;
    width: 556px;
    height: 343px;
    background: linear-gradient(160deg, var(--kraft-light), var(--kraft-dark));
  }
  .card--front { left: 330px; top: 90px; }
  .card--back  { left: 330px; top: 470px; }

  /* Front */
  .brand-block {
    position: absolute; left: 34px; top: 108px;
    display: flex; align-items: center; gap: 14px;
  }
  .brand-square { width: 26px; height: 26px; background: var(--ink); }
  .brand-name {
    font-family: "Cinzel", serif; font-weight: 700;
    font-size: 27px; line-height: 1.05; color: var(--ink);
  }
  .contact { position: absolute; left: 267px; top: 74px; width: 270px; }
  .contact-name {
    font-family: "Cinzel", serif; font-weight: 600; font-size: 24px;
    letter-spacing: 0.5px; line-height: 1;
  }
  .contact-title {
    font-family: "Roboto", sans-serif; font-size: 15px; margin-top: 12px;
  }
  .rule { width: 122px; height: 1px; background: var(--rule); }
  .rule--top { margin: 14px 0 14px; }
  .rule--bottom { margin: 16px 0 16px; }
  .contact-line {
    display: flex; align-items: center; gap: 7px;
    font-family: "Roboto", sans-serif; font-size: 15.5px; line-height: 21px;
  }
  .contact-line svg { flex: none; }
  .social-dot {
    width: 21px; height: 21px; border: 1.5px solid var(--ink);
    border-radius: 50%; flex: none;
  }

  /* Back */
  .world-map {
    position: absolute; left: 24px; top: 40px; width: 520px; height: 270px;
    background: radial-gradient(ellipse at center, var(--map-tone), transparent 72%);
  }
  .back-brand {
    position: absolute; left: 0; right: 0; top: 60px;
    display: flex; flex-direction: column; align-items: center; gap: 18px;
  }
  .back-brand .brand-square { width: 70px; height: 70px; }
  .back-brand .brand-name { font-size: 33px; letter-spacing: 1px; }
  .tagline {
    position: absolute; left: 0; right: 0; top: 237px; text-align: center;
    font-family: "Cinzel", serif; font-weight: 700; font-size: 20px;
  }
  .countries {
    position: absolute; left: 0; right: 0; top: 283px; text-align: center;
    font-family: "Roboto", sans-serif; font-size: 15.5px; letter-spacing: 0.3px;
  }
</style>
</head>
<body>
  <section class="card card--front">
    <div class="brand-block">
      <span class="brand-square"></span>
      <span class="brand-name">Pine Ledge<br>Traders</span>
    </div>
    <div class="contact">
      <h1 class="contact-name">Dale Corrigan</h1>
      <p class="contact-title">Founder - Roaming Hops Guy</p>
      <div class="rule rule--top"></div>
      <p class="contact-line">
        <svg width="14" height="11" viewBox="0 0 14 11"><rect x="0.5" y="0.5" width="13" height="10" fill="#141210"/><path d="M1 1l6 5 6-5" stroke="#c99a63" stroke-width="1.3" fill="none"/></svg>
        Dale@PineLedgeTraders.example
      </p>
      <p class="contact-line">
        <svg width="14" height="14" viewBox="0 0 14 14"><circle cx="7" cy="7" r="6.5" fill="#141210"/><path d="M0.5 7h13M7 0.5c-3 3-3 10 0 13M7 0.5c3 3 3 10 0 13" stroke="#c99a63" stroke-width="1" fill="none"/></svg>
        www.Pineledgetraders.example
      </p>
      <div class="rule rule--bottom"></div>
      <p class="contact-line">
        <span class="social-dot"></span>
        @RoamingHopsGuy
      </p>
    </div>
  </section>

  <section class="card card--back">
    <div class="world-map" role="img" aria-label="Dotted world map showing export markets"></div>
    <div class="back-brand">
      <span class="brand-square"></span>
      <span class="brand-name">PINE LEDGE TRADERS</span>
    </div>
    <p class="tagline">100% COLD CHAIN LOGISTICS</p>
    <p class="countries">AUSTRAILIA | CHINA | TAIWAN | CHILE | FRANCE | NEW ZEALAND</p>
  </section>
</body>
</html>
```